Fall Convention Graphic Designs (logo, digital brochure, t-shirt designs, social media templates)

I need a graphic package for the Redwick Movement Guild Autumn Dance Convention. Redwick Movement Guild is a non-profit organization of dance teachers, and this educational dance conference is for members and their students with multiple events throughout the weekend. The convention has a new them each year. I will need a package with a general "logo" type graphic, a digital brochure, t-shirt design, and social media graphic templates. This year's Convention has a general theme and names for each event throughout the weekend.
The theme and event names for this year are:
Convention Theme Twice Around a Waltz: Beneath the Harlow Moons
Registration Desk The Willowgate Nook
Members Welcome A Moonwashed Greeting
Banquet A Velvet Twilight
President's Reception Glow Beyond Dusk
Jr. Member Desk Wanderers' Wharf
Jr. Member Pizza Party Cricket Mixer
Members Luncheon Harlow Reveries

I am attaching a word file that includes information and text to be included in brochure. Also attached are designs from previous years for brochures, T-shirts, and social media graphics.

Colors that we will be using for decorations at various events over the weekend this year are shades of green (fern and mossy green), shades of blue (including navy), white, and pinks (including mauve). The banquet event will be decorated as an enchanted forest. We are using fairy lights, books that look like a storybook, and lanterns for decorations as well. I think I would like a more modern design, and I do not want anything that is childish or too whimsical. While we are using floral decorations I don't want bunches of flowers in the design.

*I am open to seeing initial logo type designs and giving feedback to make sure it is a direction that I like and then moving forward with the other parts of the project.

```html
<!DOCTYPE html>
<html lang="en">
<head>
<meta charset="utf-8">
<title>Redwick Movement Guild Autumn Convention Brochure</title>
<link href="https://fonts.googleapis.com/css2?family=Lora:wght@400;500&family=Urbanist:wght@400;500;600;700&family=Kaushan+Script&family=Great+Vibes&display=swap" rel="stylesheet">
<style>
:root{
  --page:#ffffff;
  --navy:#1b2e4b;
  --navy-deep:#142540;
  --card:rgba(88,118,162,.28);
  --row:rgba(110,140,185,.35);
  --pill:#5877a3;
  --ink:#ffffff;
  --soft:#dfe6f1;
  --moss:#3f5f45;
  --fern:#5f7d60;
  --icon:#7f9a86;
  --line:rgba(255,255,255,.35);
}
*{margin:0;padding:0;box-sizing:border-box}
html,body{width:1200px;height:612px;overflow:hidden;background:var(--page)}
body{position:relative;font-family:'Urbanist',sans-serif;color:var(--ink)}
.panel{position:absolute;top:54px;width:353px;height:499px;overflow:hidden}
.cover{left:47px;background:radial-gradient(ellipse 45% 70% at 70% 45%,#6b4a2e 0%,#3d2a1c 45%,#171310 80%),#171310}
.cover-art{position:absolute;inset:0;background:
  radial-gradient(circle at 9% 20%,rgba(240,150,150,.35),transparent 14%),
  radial-gradient(circle at 93% 22%,rgba(240,150,150,.35),transparent 14%),
  radial-gradient(circle at 5% 29%,rgba(255,200,60,.55),transparent 5%),
  radial-gradient(circle at 92% 33%,rgba(255,200,60,.55),transparent 6%),
  radial-gradient(ellipse 60% 20% at 40% 100%,rgba(120,160,60,.35),transparent 70%)}
.inner,.schedule,.info{background:
  radial-gradient(circle at 12% 30%,rgba(255,255,255,.5) 0 .6px,transparent 1px),
  radial-gradient(circle at 64% 12%,rgba(255,255,255,.4) 0 .6px,transparent 1px),
  radial-gradient(circle at 80% 70%,rgba(255,255,255,.4) 0 .6px,transparent 1px),
  radial-gradient(circle at 35% 85%,rgba(255,255,255,.35) 0 .6px,transparent 1px),
  var(--navy);background-size:37px 41px,53px 47px,61px 59px,43px 67px,auto}
.schedule{left:425px}
.info{left:803px}
.abs{position:absolute}
.title{left:0;width:373px;top:18px;text-align:center;font-family:'Lora',serif;font-size:19px;line-height:23px}
.date{left:103px;top:85px;font-size:14px;font-weight:600;line-height:17px}
.rule{height:1px;background:var(--line)}
.venue{left:101px;top:149px;font-size:9.6px;line-height:12.6px}
.script{font-family:'Kaushan Script',cursive}
.intensive{left:39px;top:214px;font-size:21px}
.friday{left:39px;top:245px;width:64px;height:20px;background:var(--moss);font-size:11.5px;line-height:20px;text-align:center}
.stay{left:37px;top:285px;font-size:9.6px}
.hotel{left:37px;top:300px;font-size:18px}
.address{left:37px;top:326px;font-size:9.6px;line-height:12.4px}
.call{left:38px;top:370px;font-size:9.6px;line-height:12.6px}
.phone{left:38px;top:396px;font-size:20px;font-weight:700;letter-spacing:.5px}
.online{left:38px;top:418px;font-size:9.6px}
.book{left:22px;top:447px;width:134px;height:33px;background:var(--fern);font-size:11.5px;font-weight:500;line-height:33px;text-align:center}
.theme{left:185px;width:160px;top:436px;text-align:center}
.theme .main{font-family:'Great Vibes',cursive;font-size:21px;line-height:24px}
.theme .sub{font-size:12px}
.pill{background:var(--pill);border-radius:6px;font-family:'Lora',serif;padding:0 6px;white-space:nowrap}
.names{position:absolute;left:13px;top:32px;width:325px;height:52px}
.name{position:absolute;font-family:'Lora',serif;font-size:7.4px;line-height:9px}
.name span{display:block;font-family:'Urbanist',sans-serif;font-size:5.8px;color:var(--soft);line-height:8.4px}
.vdiv{position:absolute;top:0;width:1px;height:50px;background:var(--line)}
.day{position:absolute;left:15px;width:321px;background:var(--card);border-radius:6px;padding:6px 11px}
.day h3{font-family:'Lora',serif;font-weight:400;font-size:8.6px;line-height:11px}
.day p{font-size:6px;line-height:8.5px;color:var(--soft)}
.row{display:flex;height:11.4px;align-items:center;font-size:6px;color:var(--soft)}
.row.hl{background:var(--row);width:max-content;padding-right:6px}
.row .t{width:60px;padding-left:1px}
.row small{font-size:4.6px}
.info-text{left:24px;top:64px;width:306px;font-size:6.1px;line-height:8.9px;color:var(--soft)}
.info-text p{margin-bottom:9px}
.faculty{margin-top:14px}
</style>
</head>
<body>

<section class="panel cover">
  <div class="cover-art abs" style="inset:0" role="img" aria-label="Dancer's legs en pointe in warm candlelight, framed by hanging lanterns and pink blossoms"></div>
  <h1 class="abs title">Redwick Movement Guild<br>Fall Convention</h1>

  <svg class="abs" style="left:80px;top:90px" width="14" height="14" viewBox="0 0 14 14" fill="none" stroke="var(--icon)" stroke-width="1"><rect x="1" y="2.5" width="12" height="10.5" rx="2"/><path d="M4 1v3M10 1v3"/><circle cx="4.5" cy="8" r=".6" fill="var(--icon)"/><circle cx="7" cy="8" r=".6" fill="var(--icon)"/><circle cx="9.5" cy="8" r=".6" fill="var(--icon)"/><circle cx="4.5" cy="10.5" r=".6" fill="var(--icon)"/><circle cx="7" cy="10.5" r=".6" fill="var(--icon)"/></svg>
  <div class="abs date">November<br>19 – 22, 2026</div>
  <div class="abs rule" style="left:74px;top:133px;width:152px"></div>

  <svg class="abs" style="left:76px;top:152px" width="16" height="18" viewBox="0 0 16 18" fill="none" stroke="var(--icon)" stroke-width="1.1"><path d="M8 15S3 10 3 6.5a5 5 0 0 1 10 0C13 10 8 15 8 15z"/><circle cx="8" cy="6.5" r="1.8"/><ellipse cx="8" cy="15.5" rx="6" ry="1.6"/></svg>
  <div class="abs venue">Belmere Convention Hall<br>Halden Grand Hotel,<br>Greensboro, NC</div>
  <div class="abs rule" style="left:34px;top:205px;width:152px"></div>

  <div class="abs script intensive">Teacher's Intensive</div>
  <div class="abs friday">on Friday</div>

  <svg class="abs" style="left:12px;top:288px" width="18" height="14" viewBox="0 0 18 14" fill="none" stroke="var(--icon)" stroke-width="1.1"><path d="M1 13V2M17 13V7H1"/><rect x="3" y="3.5" width="5" height="3.5" rx="1"/><rect x="10" y="3.5" width="5" height="3.5" rx="1"/></svg>
  <div class="abs stay">Outstanding accommodations at the</div>
  <div class="abs script hotel">Halden Grand Hotel</div>
  <div class="abs address">418 Linden Crest Avenue,<br>&nbsp;Greensboro, NC 27409</div>
  <div class="abs rule" style="left:14px;top:358px;width:151px"></div>

  <svg class="abs" style="left:12px;top:374px" width="19" height="19" viewBox="0 0 19 19" fill="none" stroke="var(--icon)" stroke-width="1.1"><circle cx="9.5" cy="9.5" r="8.5"/><path d="M6 5.5l1.8-.3 1 2.4-1.2.9a6 6 0 0 0 3 3l.9-1.2 2.4 1-.3 1.8c-4 .6-8.2-3.6-7.6-7.6z"/></svg>
  <div class="abs call">Call for reservations and mention<br>RMG for your best rate!</div>
  <div class="abs phone">336-555-0148</div>
  <div class="abs online">or book online.</div>

  <div class="abs book">BOOK YOUR ROOM</div>
  <div class="abs theme"><div class="main">Twice Around a Waltz</div><div class="sub">Beneath the Harlow Moons</div></div>
</section>

<section class="panel schedule">
  <div class="abs pill" style="left:13px;top:10px;height:14px;font-size:10px;line-height:14px">Convention Theme &amp; Event Names</div>
  <div class="names">
    <div class="name" style="left:0;top:0">Convention Theme<span>Twice Around a Waltz:<br>Beneath the Harlow Moons</span></div>
    <div class="name" style="left:0;top:33px">President's Reception<span>Glow Beyond Dusk</span></div>
    <div class="vdiv" style="left:78px"></div>
    <div class="name" style="left:92px;top:0">Registration Desk<span>The Willowgate Nook</span></div>
    <div class="name" style="left:92px;top:33px">Jr. Member Desk<span>Wanderers' Wharf</span></div>
    <div class="vdiv" style="left:158px"></div>
    <div class="name" style="left:169px;top:0">Members Welcome<span>A Moonwashed Greeting</span></div>
    <div class="name" style="left:169px;top:33px">Jr. Member Pizza Party<span>Cricket Mixer</span></div>
    <div class="vdiv" style="left:250px"></div>
    <div class="name" style="left:260px;top:0">Banquet<span>A Velvet Twilight</span></div>
    <div class="name" style="left:260px;top:33px">Members Luncheon<span>Harlow Reveries</span></div>
  </div>

  <div class="abs pill" style="left:15px;top:92px;height:15px;font-size:10px;line-height:15px">Schedule of Events</div>

  <div class="day" style="top:113px;height:40px">
    <h3>Thursday, November 19th</h3>
    <p>Solo Title Scholarship Competition Audition Classes, Interviews, and Opening Number Rehearsals<br>A Moonwashed Greeting- Members Welcome Party</p>
  </div>

  <div class="day" style="top:159px;height:65px">
    <h3>Friday, November 20th</h3>
    <p>Teachers Intensive<br>Solo Title Scholarship Competition Audition Classes, Interviews, and Opening Number Rehearsals<br>Registration Packet Pickup<br>Solo Title Scholarship Competition and Crowning<br>Cricket Mixer - Jr. Members Pizza and Pajama Party</p>
  </div>

  <div class="day" style="top:232px;height:134px">
    <h3>Saturday, November 21st</h3>
    <p style="margin-bottom:4px">Halden Grand Hotel, Belmere Convention Hall</p>
    <div class="row"><span class="t">8:00am</span>The Willowgate Nook - Registration Desk Opens</div>
    <div class="row hl"><span class="t">8:00am</span>Wanderers' Wharf -Junior Member Desk Opens</div>
    <div class="row"><span class="t">8:00am-8:45am</span>Junior Member Banquet Performance Rehearsal</div>
    <div class="row hl"><span class="t">9:00am-1:00pm</span>Convention Classes&nbsp; Mini</div>
    <div class="row"><span class="t">9:00am-3:00pm</span>Convention Classes&nbsp; Junior I Senior I Teachers &amp; Assistants</div>
    <div class="row hl"><span class="t">6:00pm-7:30pm</span>Banquet – A Velvet Twilight</div>
    <div class="row"><span class="t">8:30pm</span>Miss and Mr. Talent and Crowning</div>
    <div class="row hl"><span class="t">10:00pm</span>Glow Beyond Dusk - President's Reception&nbsp;<small>(Immediately following Miss / Mr. Dance Crowning)</small></div>
  </div>

  <div class="day" style="top:375px;height:112px">
    <h3>Sunday, November 22nd</h3>
    <p style="margin-bottom:4px">Halden Grand Hotel, Belmere Convention Hall</p>
    <div class="row"><span class="t">7:30am</span>Contract Signing for New Title Holders</div>
    <div class="row hl"><span class="t">8:00am-9:00am</span>Judges Critiques for New Title Holders</div>
    <div class="row"><span class="t">9:00am-1:00pm</span>Convention Classes&nbsp; Mini I Junior I Senior I Teachers &amp; Assistants</div>
    <div class="row hl"><span class="t">1:00pm-2:00pm</span>Junior Member Special Class</div>
    <div class="row"><span class="t">1:00pm</span>Harlow Reveries- Members Luncheon (Must be Pre-Registered)</div>
    <div class="row hl"><span class="t">1:00pm</span>Grand Body Meeting</div>
  </div>
</section>

<section class="panel info">
  <div class="abs pill" style="left:23px;top:28px;height:16px;font-size:11px;line-height:16px;padding:0 7px">VALUABLE INFORMATION</div>
  <div class="abs info-text">
    <p>Classroom Attire: Students &amp; teachers should be dressed in proper dance attire; leotards, tights and appropriate dance shoes. Cover ups must be worn at all times when leaving class and walking through the hotel. Tap shoes are not allowed outside of the classroom. No bare midriffs please.</p>
    <p>One badge for a parent/monitor will be given to each studio that registers Mini &amp; Junior students (one for each classroom). These people, designated by your studio, will be responsible for your Mini &amp; Junior students concerning bathroom, changing shoes, conduct, etc.</p>
    <p>Banquet Attire: Semi-formal or formal attire for students, formal attire for teachers and parents.</p>
    <p>Recommended Ages: Mini 6-3, Junior 9-13, Senior 14 &amp; up, Advanced is intended for teaching professionals.</p>
    <p>Pageant program books, banquet tickets and t-shirts must be pre-ordered.<br>**T-shirts are NOT included with Registration and must be preordered ($25). A very limited number will be available on site**</p>
    <p>Contestants in Solo Title Scholarship Competition are required to attend all classes in their age level.</p>
    <p>All members' dues must have been post-marked by September 1, 2026 to receive the member rate, You must also pre-register for the Members Luncheon on Sunday.</p>
    <p>Video recording of classes will be allowed. Video recording and photos during pageant IS NOT ALLOWED.</p>
    <p>FACULTY *I will need to be able to add in headshots for each of these people when I get them. Please leave a place holder</p>
    <p>Teachers Intensive – Featured Guest and underneath Friday November 20th<br>MARISOL VANTREE</p>
    <p class="faculty" style="line-height:9.8px">Corinne Ashby<br>Tessa Merrow<br>Juliet Marsh Ellery<br>Devon Pryor<br>To Be Determined #1</p>
  </div>
</section>

</body>
</html>
```